Book Cover for a book on Quiet Ventures

I am self-publishing my book on Brindlecart and need a book cover made. Below are the details. See attached templates for size we need to use. I also attached a previous cover we had made that I liked. The problem with it was they were two boys helping each other but the book is about women. I'm open to your ideas on the cover though, but I wanted to show you a style I liked as an idea.
Front of Cover
Book Title: Quiet Ventures
Book Subtitle: Unvarnished Notes of a Woman Founder
Author Name: Lorna T. Pelham
Add on the Spine of Cover: Quiet Ventures and Lorna T. Pelham
Back of the Cover Text:
Quiet Ventures: Unvarnished Notes of a Woman Founder is an honest account of a business owner’s experience attempting to navigate the start-up community while also pursuing spiritual growth. Author Lorna Pelham defines a spiritual entrepreneur as “someone who runs an enterprise with the purpose of growing love rather than material gain.” This book discusses the three dimensions of Quiet Ventures:
1. The business is an integral part of the founder’s spiritual journey.
2. Employees working for the spiritual enterprise, whether they know it or not, encounter this company because it's part of their spiritual path.
3. The business itself has a life force of its own and its purpose is to further the kingdom of heaven on earth.
These three dimensions happen simultaneously and work together to produce the greatest possible result. However, this can feel confusing to a founder juggling these dimensions while also trying to manage and run a business. This is not a formulaic self-help book or roadmap. Rather, it is a compilation of personal reflections that often seem at odds with the traditional world of entrepreneurship.
Below the description add my picture (see attached for my picture)
Bio text:
Lorna Pelham founded Halvex with the vision of ushering in a life-long education system that shifts away from standardization to one that empowers people to live their purpose. In college, Lorna interned for Open Meadow, a women’s empowerment initiative where she recognized her passion for helping people find their voice. Lorna's 20-year journey has come full circle to empowering other female CEOs who are pursuing the path of Quiet Ventures.
NOTE: Please note that Brindlecart puts a bar code on the bottom right of the back cover as is noted on the attached template.
Size template is attached to the brief, here are the sizes typed out:
# Description Width (in) Height (in)
1 Full Cover 12.79 9.25
2 Front Cover 6 9
3 Safe Area 5.875 8.75
4 Bleed 0.125 0.125
5 Margin 0.125 0.125
6 Spine 0.54 9
7 Spine Safe Area 0.415 8.75
8 Spine Margin 0.062 0.062
9 Barcode Margin 0.25 0.25
Pre-publication checklist
BRINDLECART TIPS for the final cover:
1. Save as a PDF. Your cover must be a single PDF that includes the back cover, spine, and front cover as one image.
2. Flatten all transparencies. These can cause the file to print with missing or distorted content. Consult your software's documentation to learn how.
3. Embed your fonts. Consult your software's documentation to learn how.
4. Remove crop marks, color bars, template text. Crop marks are lines showing where pages should be trimmed. Color bars are strips with a series of patches used to ensure color balance during printing. Also, remove any template text, PDF creation guides, or software references.
5. Ensure your cover image meets the minimum resolution of 300 DPI (dots per inch).
6. Optimize PDFs. Optimization is useful to reduce your file size, allowing for higher performance when transferring, uploading, viewing, and printing the files.
7. Remove file security. Locked or encrypted files will fail review.
Target Market(s)
Women who want to be CEOs or are currently CEOs of companies.
Industry/Entity Type
Entrepreneurship, business, spirituality
Requirements
Must have
- Just the text on the description. A very welcoming feel.
Nice to have
- I like the idea of having a sunrise/sunset in the image somehow like in the example I attached to the brief, but again I'm open.
Should not have
- Please don't put any yoga or meditation poses or hands outstretched. I have a lot of interesting ones that look like my example so if you are going to submit after Saturday 10/29, please only do so if you have a new idea! Thanks!

```html
<!DOCTYPE html>
<html lang="en">
<head>
<meta charset="utf-8">
<title>Quiet Ventures – Book Cover</title>
<link href="https://fonts.googleapis.com/css2?family=Cinzel:wght@400;700&family=Cormorant+Garamond:ital,wght@1,500&family=Crimson+Text:wght@400;700&display=swap" rel="stylesheet">
<style>
  :root {
    --pink: #fb476c;
    --ink: #111111;
    --paper: #ffffff;
    --backdrop: #7ea7b3;
    --text: #1c1c1c;
    --barcode-line: #f6a9b9;
    --spine-edge: #f3f3f3;
  }
  * { margin: 0; padding: 0; box-sizing: border-box; }
  html, body { width: 1200px; height: 900px; overflow: hidden; }
  body { background: var(--backdrop); position: relative; }

  .cover {
    position: absolute; left: 20px; top: 33px;
    width: 1160px; height: 833px;
    background: var(--paper);
    font-family: "Crimson Text", Georgia, serif;
    color: var(--text);
  }
  .abs { position: absolute; }

  .title-main, .title-sub, .author-name, .spine-title, .spine-author {
    font-family: "Cinzel", "Times New Roman", serif;
    text-transform: uppercase;
  }
  .title-main { color: var(--pink); font-weight: 400; line-height: 1; text-align: center; }
  .title-sub { color: var(--ink); font-weight: 700; line-height: 1; text-align: center; }
  .subtitle {
    font-family: "Cormorant Garamond", Georgia, serif;
    font-style: italic; font-weight: 500; text-align: center; color: var(--ink);
    white-space: nowrap;
  }
  .rule { height: 1.5px; background: var(--pink); }

  /* back cover */
  .back-title { left: 30px; width: 500px; top: 50px; font-size: 50px; letter-spacing: 1px; }
  .back-title-sub { left: 30px; width: 500px; top: 104px; font-size: 24px; letter-spacing: 1px; }
  .back-rule-top { left: 150px; width: 260px; top: 143px; }
  .back-subtitle { left: 130px; width: 300px; top: 146px; font-size: 17px; line-height: 22px; }
  .back-rule-bottom { left: 150px; width: 260px; top: 171px; }

  .blurb {
    left: 54px; width: 446px; top: 196px;
    font-size: 10.6px; line-height: 12.8px; text-align: justify; hyphens: auto;
  }
  .blurb p + ol, .blurb ol + p { margin-top: 13px; }
  .dimensions { list-style: none; font-weight: 700; padding-left: 22px; }
  .dimensions li { position: relative; padding-left: 22px; }
  .dimensions li span { position: absolute; left: 0; font-weight: 400; }

  .back-divider { left: 155px; width: 245px; top: 437px; }

  .author-photo {
    left: 26px; top: 480px; width: 210px; height: 287px;
    background: radial-gradient(ellipse at 45% 38%, #d9a88d 0%, #9b6247 40%, #f0f0ee 74%);
    border-radius: 48% 48% 0 0 / 35% 35% 0 0;
    overflow: hidden;
  }
  .author-photo::after {
    content: ""; position: absolute; left: 0; right: 0; bottom: 0; height: 100px;
    background: #f2566f; border-radius: 40% 40% 0 0 / 45% 45% 0 0;
  }

  .bio {
    left: 252px; width: 248px; top: 479px;
    font-size: 10.6px; line-height: 12.8px; text-align: justify; hyphens: auto;
  }
  .barcode-area { left: 334px; top: 650px; width: 176px; height: 97px; border: 1px solid var(--barcode-line); }

  /* spine */
  .spine { left: 555px; top: 0; width: 50px; height: 767px; border-left: 1px solid var(--spine-edge); border-right: 1px solid var(--spine-edge); }
  .spine-title {
    left: 12px; top: 64px; writing-mode: vertical-rl;
    font-size: 24px; letter-spacing: 2px; line-height: 26px; white-space: nowrap;
  }
  .spine-title .accent { color: var(--pink); }
  .spine-title .dark { color: var(--ink); font-weight: 700; }
  .spine-author {
    left: 14px; top: 500px; writing-mode: vertical-rl;
    font-size: 19px; letter-spacing: 1.5px; line-height: 22px; color: var(--pink); white-space: nowrap;
  }

  /* front cover */
  .front-title { left: 620px; width: 540px; top: 58px; font-size: 84px; letter-spacing: 2px; }
  .front-title-sub { left: 620px; width: 540px; top: 150px; font-size: 40px; letter-spacing: 2px; }
  .front-rule-top { left: 680px; width: 400px; top: 214px; }
  .front-subtitle { left: 640px; width: 480px; top: 220px; font-size: 27px; line-height: 34px; }
  .front-rule-bottom { left: 680px; width: 400px; top: 260px; }

  .front-emblem {
    left: 708px; top: 311px; width: 349px; height: 403px;
    background:
      radial-gradient(circle at 48% 42%, rgba(255,255,255,0.9) 0 4%, transparent 5%),
      linear-gradient(160deg, #ee2f6d 0%, #f5872a 25%, #f7d21c 42%, #8fc73e 58%, #19a7d9 74%, #5b2d91 100%);
    border-radius: 50% 50% 12% 12% / 45% 45% 10% 10%;
    opacity: 0.9;
  }

  .author-band { left: 0; top: 767px; width: 1160px; height: 66px; background: var(--pink); }
  .author-name {
    left: 620px; width: 540px; top: 776px;
    font-size: 38px; letter-spacing: 3px; color: var(--paper); text-align: center; line-height: 48px;
  }
</style>
</head>
<body>
  <div class="cover">
    <!-- back cover -->
    <h2 class="abs title-main back-title">Quiet</h2>
    <div class="abs title-sub back-title-sub">Ventures</div>
    <div class="abs rule back-rule-top"></div>
    <div class="abs subtitle back-subtitle">Unvarnished Notes of a Woman Founder</div>
    <div class="abs rule back-rule-bottom"></div>

    <div class="abs blurb">
      <p>Quiet Ventures: Unvarnished Notes of a Woman Founder is an honest account of a business owner’s experience attempting to navigate the start-up community while also pursuing spiritual growth. Author Lorna Pelham defines a spiritual entrepreneur as “someone who runs an enterprise with the purpose of growing love rather than material gain.” This book discusses the three dimensions of Quiet Ventures:</p>
      <ol class="dimensions">
        <li><span>1.</span>The business is an integral part of the founder’s spiritual journey.</li>
        <li><span>2.</span>Employees working for the spiritual enterprise, whether they know it or not, encounter this company because it's part of their spiritual path.</li>
        <li><span>3.</span>The business itself has a life force of its own and its purpose is to further the kingdom of heaven on earth.</li>
      </ol>
      <p>These three dimensions happen simultaneously and work together to produce the greatest possible result. However, this can feel confusing to a founder juggling these dimensions while also trying to manage and run a business. This is not a formulaic self-help book or roadmap. Rather, it is a compilation of personal reflections that often seem at odds with the traditional world of entrepreneurship.</p>
    </div>

    <div class="abs rule back-divider"></div>

    <div class="abs author-photo" role="img" aria-label="Portrait photo of the author, smiling, long brown hair, pink top"></div>

    <p class="abs bio">Lorna Pelham founded Halvex with the vision of ushering in a life-long education system that shifts away from standardization to one that empowers people to live their purpose. In college, Lorna interned for Open Meadow, a women’s empowerment initiative where she recognized her passion for helping people find their voice. Lorna's 20-year journey has come full circle to empowering other female CEOs who are pursuing the path of Quiet Ventures.</p>

    <div class="abs barcode-area"></div>

    <!-- spine -->
    <div class="abs spine">
      <div class="abs spine-title"><span class="accent">Quiet</span> <span class="dark">Ventures</span></div>
      <div class="abs spine-author">Lorna T. Pelham</div>
    </div>

    <!-- front cover -->
    <h1 class="abs title-main front-title">Quiet</h1>
    <div class="abs title-sub front-title-sub">Ventures</div>
    <div class="abs rule front-rule-top"></div>
    <div class="abs subtitle front-subtitle">Unvarnished Notes of a Woman Founder</div>
    <div class="abs rule front-rule-bottom"></div>

    <div class="abs front-emblem" role="img" aria-label="Illustration of a head silhouette with a circular arrow and rainbow-coloured arrows radiating outward"></div>

    <div class="abs author-band"></div>
    <div class="abs author-name">Lorna T. Pelham</div>
  </div>
</body>
</html>
```